Business Card Design Project

We need a business card for a new technology services company. We develop software and implement software packages for our business customers and although we will begin with just one or two service offerings, our service offerings will expand over time. Our name comes from the an author, KL Barrow, and his "idea" was that opportunity should be based on ability and achievement, not on social status.

We would like to see a design that is standard in its size and shape, but stands apart in its dramatic color contrasts. The card should not use too many colors - the colors used in the background should highlight the brilliant blues of the logo (see attachment) to dramatic effect. The background should not be white.

If necessary, you can change the color of the words "KL Barrow", but not the word "Idea".

Card size should be U.S. standard 2 inches by 3.5 inches and provide for 1/8 inch bleed area on each side.

We need a design for both sides of the business card, one side communicating the company logo and contact information, the other side being purely graphical, incorporating the logo but no other information.

Contact Information Required:
Kate Brook
KateBrook@klbarrowvista.com
614-387-2259

Target Market(s)

Business executives

Industry/Entity Type

Software

Requirements
Must have
• It must have the full company logo on one side, and at least the graphic element of the logo on the other. Either that or the full logo on both.
Nice to have
• It would be nice to have a design that could work without needing two different textures. For example, it would be nice if the entire card could be shiny, not just parts of the card.

It would also be nice if texture is something we could add later.
Should not have
• The card should not use the color green.

```html
<!DOCTYPE html>
<html lang="en">
<head>
<meta charset="utf-8">
<title>Barrow Vista — Business Card</title>
<link href="https://fonts.googleapis.com/css2?family=Crimson+Pro:ital,wght@0,700;1,700&display=swap" rel="stylesheet">
<style>
  :root {
    --backdrop: #ccccff;
    --card-black: #000000;
    --brand-cyan: #00cfe6;
    --band-grey: #9a9a9a;
    --text-white: #ffffff;
  }
  html, body {
    margin: 0;
    padding: 0;
    width: 1200px;
    height: 728px;
    overflow: hidden;
    background: var(--backdrop);
  }
  .canvas {
    position: relative;
    width: 1200px;
    height: 728px;
  }
  .card {
    position: absolute;
    width: 494px;
    height: 282px;
    border-radius: 40px;
    background: var(--card-black);
    overflow: hidden;
  }
  .card--front { left: 355px; top: 45px; }
  .card--back  { left: 350px; top: 400px; }

  .card__bands {
    position: absolute;
    left: 0; top: 0;
    width: 494px; height: 282px;
  }

  .brand {
    position: absolute;
    display: flex;
    align-items: center;
    gap: 16px;
  }
  .brand__name {
    font-family: "Crimson Pro", Georgia, serif;
    font-style: normal;
    font-weight: 700;
    font-size: 44px;
    letter-spacing: 1px;
    color: var(--brand-cyan);
    line-height: 1;
    white-space: nowrap;
  }
  .brand__dot {
    width: 30px;
    height: 30px;
    border-radius: 50%;
    background: var(--brand-cyan);
  }
  .card--front .brand { left: 48px; top: 130px; }
  .card--back .brand  { left: 40px; top: 168px; }

  .identity {
    position: absolute;
    left: 110px;
    top: 229px;
    width: 122px;
    text-align: center;
    font-family: "Crimson Pro", Georgia, serif;
    font-style: italic;
    font-weight: 700;
    color: var(--text-white);
  }
  .identity__title {
    font-size: 20px;
    letter-spacing: 2px;
    line-height: 1.15;
  }
  .identity__name {
    font-size: 18px;
    line-height: 1.15;
  }

  .divider {
    position: absolute;
    left: 257px;
    top: 227px;
    width: 3px;
    height: 50px;
    background: var(--band-grey);
  }

  .contact {
    position: absolute;
    left: 271px;
    top: 233px;
    font-family: "Crimson Pro", Georgia, serif;
    font-style: italic;
    font-weight: 700;
    font-size: 13.5px;
    color: var(--text-white);
    list-style: none;
    margin: 0;
    padding: 0;
  }
  .contact__item {
    display: flex;
    align-items: center;
    gap: 5px;
    height: 22px;
  }
  .contact__icon {
    width: 14px;
    height: 16px;
    flex: none;
  }
  .contact__at {
    font-family: Arial, sans-serif;
    font-style: normal;
    font-weight: 700;
    font-size: 17px;
    color: var(--brand-cyan);
    width: 14px;
  }

  .back-email {
    position: absolute;
    margin: 0;
    left: 0;
    width: 494px;
    top: 219px;
    text-align: center;
    font-family: "Crimson Pro", Georgia, serif;
    font-style: italic;
    font-weight: 700;
    font-size: 14px;
    color: var(--text-white);
  }
  .back-email__domain { color: var(--brand-cyan); }
</style>
</head>
<body>
<main class="canvas">

  <section class="card card--front" aria-label="Card front">
    <svg class="card__bands" viewBox="0 0 494 282" aria-hidden="true">
      <polygon points="0,0 494,0 494,72 405,13 0,104" fill="var(--brand-cyan)"/>
      <polygon points="0,104 405,13 494,72 494,82 405,20 0,112" fill="var(--card-black)"/>
      <polygon points="0,112 405,20 494,82 494,104 405,25 0,141" fill="var(--band-grey)"/>
    </svg>

    <div class="brand">
      <span class="brand__name">Barrow Vista</span>
      <span class="brand__dot"></span>
    </div>

    <div class="identity">
      <div class="identity__title">Precedent</div>
      <div class="identity__name">Kate Brook</div>
    </div>

    <div class="divider"></div>

    <ul class="contact">
      <li class="contact__item">
        <svg class="contact__icon" viewBox="0 0 14 16" aria-hidden="true">
          <path d="M4 1 L6 4.5 L4.5 6 C5 8.5 6.5 10.5 8.5 11.5 L10 10 L13 12.5 L11 15 C6 14.5 1.5 9 2 2.5 Z" fill="var(--brand-cyan)"/>
        </svg>
        <span>614-387-2259</span>
      </li>
      <li class="contact__item">
        <span class="contact__at">@</span>
        <span>KateBrook@klbarrowvista.com</span>
      </li>
    </ul>
  </section>

  <section class="card card--back" aria-label="Card back">
    <div class="brand">
      <span class="brand__name">Barrow Vista</span>
      <span class="brand__dot"></span>
    </div>
    <p class="back-email">KateBrook@<span class="back-email__domain">klbarrowvista</span>.com</p>
  </section>

</main>
</body>
</html>
```